Additional Benefits of Working for VELMAR

Please prepare an infographic on the additional benefits besides salary of working at VELMAR as detailed in the attached word document. Also attached is our logo in eps and our company design "Grounds". We are a Not For Profit company that finds jobs for unemployed people of government benefit payments

Target Market(s)

Attracting people to work for VELMAR. Making VELMAR an employer of choice.

Font styles to use
Sans Serif

Colors

Designer to choose colors to be used in the design.

Requirements
Must have
• be on 1 page
• have our logo
Nice to have
• Our Grounds design worked into it.
• Happy engaged employees
• Community engagement - we are a not for profit organisation
Should not have
• Discrimination, swearing,

```html
<!DOCTYPE html>
<html lang="en">
<head>
<meta charset="utf-8">
<title>The Benefits of Working with Us – VELMAR</title>
<link href="https://fonts.googleapis.com/css2?family=Questrial&display=swap" rel="stylesheet">
<style>
  :root {
    --green: #15a07c;
    --green-dark: #0d6b53;
    --orange: #c68a34;
    --orange-light: #e8b666;
    --text: #2b2b2b;
    --paper: #ffffff;
    --ground-a: #f1f2f0;
    --ground-b: #e3e6e2;
    --card-a: #f4f1ea;
    --card-b: #dcdcd6;
  }
  * { box-sizing: border-box; margin: 0; padding: 0; }
  html, body { width: 1200px; height: 1053px; overflow: hidden; background: var(--paper); }
  body { position: relative; font-family: "Questrial", "Century Gothic", sans-serif; color: var(--text); }

  .poster {
    position: absolute; left: 173px; top: 97px; width: 842px; height: 783px;
    background: radial-gradient(circle at 60% 55%, var(--ground-b), var(--ground-a) 70%);
    box-shadow: 4px 6px 10px rgba(0,0,0,.35);
  }
  .title {
    position: absolute; left: 423px; top: 112px; width: 575px; height: 68px;
    border-radius: 22px;
    background: linear-gradient(180deg, var(--green), var(--green-dark));
    color: #fff; font-size: 36px; letter-spacing: .5px;
    display: flex; align-items: center; justify-content: center;
  }
  .brand {
    position: absolute; left: 198px; top: 107px; width: 170px; height: 170px;
    border-radius: 50%; background: #fff;
    display: flex; align-items: center; justify-content: center;
  }
  .brand-name { font-size: 40px; font-weight: 400; color: #111; letter-spacing: -1px; }

  .links { position: absolute; left: 0; top: 0; width: 1200px; height: 1053px; }

  .card {
    position: absolute; border: 4px solid var(--orange); border-radius: 18px; overflow: hidden;
    background: linear-gradient(160deg, var(--card-a), var(--card-b));
    box-shadow: 1px 2px 4px rgba(0,0,0,.25);
  }
  .card-head {
    background: linear-gradient(180deg, var(--orange-light), var(--orange));
    color: #fff; font-size: 16px; line-height: 20px; text-align: center;
    padding: 6px 4px 4px;
  }
  .card-body { padding: 8px 6px 6px 7px; font-size: 10.4px; line-height: 14px; }
  .card-body p { margin-bottom: 6px; }
  .card-body p::before { content: "• "; }

  .icon-ring {
    position: absolute; width: 104px; height: 104px; border-radius: 50%;
    border: 4px solid var(--green); background: #fff;
  }
</style>
</head>
<body>
  <div class="poster" role="img" aria-label="Soft background in the company Grounds design tones"></div>

  <svg class="links" viewBox="0 0 1200 1053" aria-hidden="true">
    <g stroke="var(--green)" stroke-width="4" fill="none">
      <line x1="473" y1="317" x2="473" y2="360"/>
      <line x1="525" y1="253" x2="593" y2="253"/>
      <line x1="770" y1="248" x2="830" y2="248"/>
      <line x1="900" y1="322" x2="900" y2="360"/>
      <line x1="666" y1="447" x2="666" y2="486"/>
      <line x1="572" y1="530" x2="622" y2="530"/>
      <line x1="722" y1="525" x2="794" y2="525"/>
      <line x1="272" y1="514" x2="272" y2="546"/>
      <line x1="333" y1="569" x2="394" y2="569"/>
      <line x1="283" y1="646" x2="283" y2="686"/>
      <line x1="502" y1="593" x2="502" y2="622"/>
      <line x1="700" y1="586" x2="700" y2="628"/>
      <line x1="772" y1="668" x2="793" y2="668"/>
      <path d="M900 780 V815 Q900 830 885 830 H731"/>
    </g>
  </svg>

  <div class="brand"><span class="brand-name">VELMAR</span></div>
  <div class="title">The Benefits of Working with Us</div>

  <div class="icon-ring" style="left:421px;top:213px"></div>
  <div class="icon-ring" style="left:828px;top:220px"></div>
  <div class="icon-ring" style="left:231px;top:544px"></div>
  <div class="icon-ring" style="left:620px;top:484px"></div>
  <div class="icon-ring" style="left:629px;top:756px"></div>

  <svg class="links" viewBox="0 0 1200 1053" aria-hidden="true">
    <g stroke="var(--green)" stroke-width="3.5" fill="none" stroke-linejoin="round" stroke-linecap="round">
      <path d="M473 290 L452 269 Q442 256 452 246 Q463 236 473 249 Q483 236 494 246 Q504 256 494 269 Z"/>
      <path d="M473 283 L457 267 Q450 258 457 251 Q465 244 473 254 Q481 244 489 251 Q496 258 489 267 Z"/>
      <rect x="861" y="252" width="40" height="42" rx="3"/>
      <line x1="865" y1="258" x2="897" y2="258"/>
      <rect x="886" y="268" width="15" height="12" rx="2"/>
      <line x1="283" y1="570" x2="283" y2="612"/>
      <line x1="262" y1="580" x2="304" y2="580"/>
      <path d="M262 580 L254 598 H270 Z"/>
      <path d="M304 580 L296 598 H312 Z"/>
      <rect x="274" y="612" width="18" height="5"/>
      <rect x="650" y="512" width="46" height="46"/>
      <line x1="658" y1="550" x2="658" y2="538"/>
      <line x1="667" y1="550" x2="667" y2="530"/>
      <line x1="676" y1="550" x2="676" y2="535"/>
      <line x1="685" y1="550" x2="685" y2="525"/>
      <path d="M654 535 L668 522 L677 530 L694 513"/>
      <path d="M686 513 H694 V521"/>
      <path d="M671 784 V798 L681 804 L691 798 V784 Z"/>
      <circle cx="681" cy="818" r="13"/>
      <path d="M681 811 L684 816 L689 817 L685 821 L686 826 L681 823 L676 826 L677 821 L673 817 L678 816 Z"/>
    </g>
  </svg>

  <section class="card" style="left:196px;top:248px;width:180px;height:267px">
    <h2 class="card-head">Life Balance</h2>
    <div class="card-body">
      <p>VELMAR Day Leave. An extra day of at Christmas</p>
      <p>BIRTHDAY Leave. A paid day off on your birthday</p>
      <p>A day off every month as Time in Lieu</p>
      <p>4 weeks Annual Leave</p>
      <p>Genereous Personal Leave</p>
      <p>Support for parental leave for the birth or adoption of a child</p>
      <p>Flexible work arrangements</p>
    </div>
  </section>

  <section class="card" style="left:392px;top:357px;width:180px;height:236px">
    <h2 class="card-head">Wellbeing</h2>
    <div class="card-body">
      <p>Up to $450 per year to spend on Wellbeing services such as gym or yoga memberships</p>
      <p>Free counselling services 24x7 via our Employee Assistance Program</p>
      <p>Discount private health insurance</p>
      <p>WHS policies which support a safe, inclusive work place</p>
    </div>
  </section>

  <section class="card" style="left:591px;top:213px;width:180px;height:234px">
    <h2 class="card-head">Career Growth<br>&amp;Professional<br>Development</h2>
    <div class="card-body">
      <p>Ongoing internal training and development opportunities</p>
      <p>External study support &amp; study leave</p>
      <p>Access to the tools and technology to do your job well</p>
      <p>Career advancement opportunities</p>
      <p>Internal job vacancy listing</p>
    </div>
  </section>

  <section class="card" style="left:792px;top:357px;width:179px;height:206px">
    <h2 class="card-head">Remuneration<br>&amp; Salary Packaging</h2>
    <div class="card-body">
      <p>Competetive salary</p>
      <p>Ability to salary package up to $15,900 and reduce your tax. Package rent, home loans, child care and much more</p>
      <p>Salary package up to $2,650 on meal entertainment and holiday accommodation</p>
    </div>
  </section>

  <section class="card" style="left:194px;top:683px;width:180px;height:158px">
    <h2 class="card-head">Diversity &amp; Inclusion</h2>
    <div class="card-body">
      <p>An inclusive and diverse culture where different backgounds, experiences and perspectives are valued</p>
      <p>Gender diversity. Over 50% of our workforce and our leaders are female</p>
    </div>
  </section>

  <section class="card" style="left:391px;top:620px;width:180px;height:215px">
    <h2 class="card-head">Benefits</h2>
    <div class="card-body">
      <p>Discounted vouchers for Marlo, Greenleaf, Soundcrest, Reelhouse, Cellar Lane, ValuMart, Trailpoint and many others via Paywise e-wallet</p>
      <p>A range of other employee discounts are also available, including access to discounted bankin and finance, vehicle purchasing, leasing and hotel accomodation</p>
    </div>
  </section>

  <section class="card" style="left:592px;top:625px;width:180px;height:120px">
    <h2 class="card-head">Recognition</h2>
    <div class="card-body">
      <p>We celebrate our people forreaching service milestones</p>
      <p>Team &amp; individual recognition for high performance</p>
    </div>
  </section>

  <section class="card" style="left:791px;top:592px;width:180px;height:188px">
    <h2 class="card-head">Contributing to<br>Community</h2>
    <div class="card-body">
      <p>Team involvement in local charity and community events</p>
      <p>Participation in VELMAR's 1000 Jobs in 100 days</p>
      <p>Strong relationships and connection with Indigenous Communities in support of Indigenous Emplyment</p>
    </div>
  </section>
</body>
</html>
```